Motel Sign - Front

(21/03/12 - I've edited the brief and removing the words "garden view" its not fitting in the designs I'm getting and just want the word motel to be the focus. I have a template/vision of what I want - see the whiteboard sketch of what I'm looking for uploaded today. Definitely open to creatively, new designs and different ideas but the whiteboard design I've done should be a guideline. Keep it fresh/green/white. use the sample photos of green as inspiration. Thanks)
We are a motel set in the mountain country of Victoria - Australia. The front of the motel needs a fresh look. We recently removed a large amount of the garden to expose a brick courtyard fence which the front of the courtyard faces out to the main road. Within the courtyard fence there is a wooden frame and paneling.
We want to have a new sign created to slot into the wooden frame. (see photo) its the white component.
Its a very large and unusual shape and I want to keep it simple but need to fill the in the best way possible.
The space is 940mm high and 4940mm width.
The message of the sign is simple the word "MOTEL". I want people to be able to drive past and glance in and see we are a motel straight away. So the main purpose of the sign is to say "MOTEL".
I am open to colour use to match the space and have impact. I thought a background colour should be 'off white'. I'm open to the colours used to match your design as long as it matches the brief. Maybe a garden green for the emblem.
IN BRIEF:
1) the word "MOTEL"
2) Border/Background that ties in the garden.
The design should be centred, clean and simple, doesn't have to fill the whole space as long as its balanced and centred.
I like cursive and garden like designs for this one - as long its the word MOTEL still has impact. (OPEN TO NEW IDEAS)
I am also open to different ideas and suggestions if you feel you have a better way to take advantage of this space.
The sign will be 7-8 metres from the road itself.
NOTE: the photos show the space and the painted white in the space where the sign will go. The garden in front of this space will be completely cleared.
Motel

```html
<!DOCTYPE html>
<html lang="en">
<head>
<meta charset="utf-8">
<title>Motel Sign – Front Concepts</title>
<link rel="stylesheet" href="https://fonts.googleapis.com/css2?family=Russo+One&family=Ultra&display=swap">
<style>
  :root {
    --page: #ffffff;
    --leaf-light: #e2e87a;
    --leaf-mid: #b5d35a;
    --leaf-deep: #5fb53a;
    --garden-dark: #003311;
    --letter-white: #ffffff;
    --label-ink: #000000;
  }
  html, body {
    margin: 0;
    padding: 0;
    width: 1200px;
    height: 685px;
    overflow: hidden;
    background: var(--page);
  }
  .board {
    position: relative;
    width: 1200px;
    height: 685px;
  }
  .sign {
    position: absolute;
    left: 70px;
    width: 1096px;
    height: 210px;
  }
  .sign--block { top: 22px; }
  .sign--slab { top: 380px; height: 208px; }
  .sign__garden {
    position: absolute;
    inset: 0;
    background:
      radial-gradient(ellipse 30% 80% at 50% 40%, var(--leaf-light) 0%, transparent 70%),
      radial-gradient(ellipse 22% 70% at 8% 70%, var(--leaf-deep) 0%, transparent 75%),
      radial-gradient(ellipse 22% 70% at 94% 70%, var(--leaf-deep) 0%, transparent 75%),
      linear-gradient(90deg, var(--leaf-mid), var(--leaf-light) 40%, var(--leaf-mid) 60%, var(--leaf-mid));
  }
  .sign__word {
    position: absolute;
    inset: 0;
    width: 100%;
    height: 100%;
  }
  .word--block {
    font-family: "Russo One", sans-serif;
    font-size: 160px;
    fill: var(--garden-dark);
    stroke: var(--letter-white);
    stroke-width: 3px;
    paint-order: stroke;
  }
  .word--slab {
    font-family: "Ultra", serif;
    font-size: 150px;
    fill: var(--letter-white);
    stroke: var(--garden-dark);
    stroke-width: 9px;
    stroke-linejoin: round;
    paint-order: stroke;
  }
  .word--slab-shadow {
    font-family: "Ultra", serif;
    font-size: 150px;
    fill: var(--garden-dark);
    stroke: var(--garden-dark);
    stroke-width: 9px;
    stroke-linejoin: round;
  }
  .option-label {
    position: absolute;
    left: 0;
    width: 100%;
    margin: 0;
    text-align: center;
    font-family: "Ultra", serif;
    font-size: 30px;
    line-height: 1;
    color: var(--label-ink);
  }
  .option-label--3 { top: 236px; }
  .option-label--4 { top: 598px; }
</style>
</head>
<body>
<main class="board">
  <section class="sign sign--block">
    <div class="sign__garden" role="img" aria-label="Green garden background with white vine swirls and leafy fronds"></div>
    <svg class="sign__word" viewBox="0 0 1096 210" aria-label="MOTEL">
      <text class="word--block" x="166" y="166" textLength="766" lengthAdjust="spacingAndGlyphs">MOTEL</text>
    </svg>
  </section>
  <p class="option-label option-label--3">3</p>

  <section class="sign sign--slab">
    <div class="sign__garden" role="img" aria-label="Green garden background with white vine swirls and leafy fronds"></div>
    <svg class="sign__word" viewBox="0 0 1096 208" aria-label="MOTEL">
      <text class="word--slab-shadow" x="236" y="159" textLength="618" lengthAdjust="spacingAndGlyphs" aria-hidden="true">MOTEL</text>
      <text class="word--slab" x="230" y="153" textLength="618" lengthAdjust="spacingAndGlyphs">MOTEL</text>
    </svg>
  </section>
  <p class="option-label option-label--4">4</p>
</main>
</body>
</html>
```